Redesign of business card for Cedar Ridge Mechanical

We are looking for a new design for our business cards for Cedar Ridge Mechanical. We are a plumbing & HVAC construction company, operating on the West Coast of Canada and USA. Logo attached.
Industry/Entity Type
Construction - Plumbing & HVAC
Contact Information for Business Card
Name, address, phone numbers, email, website address
Look and feel
Each slider illustrates characteristics of the customer's brand and the style your logo design should communicate.

```html
<!DOCTYPE html>
<html lang="en">
<head>
<meta charset="utf-8">
<title>Cedar Ridge Mechanical – Business Card</title>
<link rel="stylesheet" href="https://fonts.googleapis.com/css2?family=Open+Sans:wght@400;700&display=swap">
<style>
  :root {
    --page-bg: #ece8e3;
    --panel-dark: #2e2b29;
    --panel-dark-2: #4a4541;
    --crescent: #8c857d;
    --panel-light: #ddd5cb;
    --text-warm: #dccbb4;
    --text-soft: #cdbda8;
    --brand-ink: #1f1d1b;
  }
  * { margin: 0; padding: 0; box-sizing: border-box; }
  html, body {
    width: 1200px;
    height: 1047px;
    overflow: hidden;
    background: var(--page-bg);
    font-family: "Open Sans", Arial, sans-serif;
  }
  .card {
    position: absolute;
    left: 100px;
    top: 243px;
    width: 1000px;
    height: 560px;
    border-radius: 26px;
    overflow: hidden;
    box-shadow: 0 18px 40px rgba(0,0,0,0.18);
  }
  .card-shapes {
    position: absolute;
    inset: 0;
    display: block;
  }
  .holder {
    position: absolute;
    left: 53px;
    top: 88px;
    color: var(--text-warm);
  }
  .holder-name {
    font-size: 33px;
    font-weight: 700;
    letter-spacing: 0.5px;
    line-height: 1.1;
  }
  .holder-title {
    font-size: 23px;
    font-weight: 400;
    color: var(--text-soft);
    margin-top: 2px;
  }
  .address {
    position: absolute;
    left: 45px;
    top: 212px;
    font-size: 25px;
    line-height: 34px;
    color: var(--text-soft);
  }
  .contacts {
    position: absolute;
    left: 43px;
    top: 330px;
    list-style: none;
    color: var(--text-soft);
    font-size: 25px;
    line-height: 35px;
  }
  .contacts li {
    display: flex;
    align-items: center;
    gap: 10px;
  }
  .contacts svg { width: 20px; height: 20px; flex: none; }
  .brand {
    position: absolute;
    left: 500px;
    top: 170px;
    width: 470px;
    display: flex;
    align-items: center;
    gap: 22px;
    color: var(--brand-ink);
  }
  .brand-square {
    width: 92px;
    height: 92px;
    border: 10px solid var(--brand-ink);
    border-radius: 12px;
    flex: none;
  }
  .brand-name {
    font-size: 44px;
    font-weight: 700;
    line-height: 1.05;
    text-transform: uppercase;
    letter-spacing: 1px;
  }
</style>
</head>
<body>
  <section class="card" aria-label="Cedar Ridge Mechanical business card">
    <svg class="card-shapes" viewBox="0 0 1000 560" aria-hidden="true">
      <defs>
        <linearGradient id="darkPanel" x1="0" y1="0" x2="1" y2="1">
          <stop offset="0" stop-color="var(--panel-dark-2)"/>
          <stop offset="1" stop-color="var(--panel-dark)"/>
        </linearGradient>
        <linearGradient id="crescentTone" x1="0" y1="0" x2="1" y2="0">
          <stop offset="0" stop-color="#6f6963"/>
          <stop offset="1" stop-color="var(--crescent)"/>
        </linearGradient>
      </defs>
      <rect class="dark-panel" width="1000" height="560" fill="url(#darkPanel)"/>
      <circle class="crescent" cx="715" cy="280" r="292" fill="url(#crescentTone)"/>
      <rect class="light-panel" x="748" y="0" width="252" height="560" fill="var(--panel-light)"/>
      <circle class="light-panel" cx="748" cy="280" r="280" fill="var(--panel-light)"/>
    </svg>

    <div class="holder">
      <p class="holder-name">DANIEL HAYES</p>
      <p class="holder-title">Managing Director</p>
    </div>

    <p class="address">Your address, City<br>State, Zip 1234</p>

    <ul class="contacts">
      <li>
        <svg viewBox="0 0 24 24" aria-hidden="true"><path fill="currentColor" d="M6.6 10.8c1.4 2.8 3.8 5.1 6.6 6.6l2.2-2.2c.3-.3.7-.4 1-.2 1.1.4 2.3.6 3.6.6.6 0 1 .4 1 1V20c0 .6-.4 1-1 1C10.6 21 3 13.4 3 4c0-.6.4-1 1-1h3.5c.6 0 1 .4 1 1 0 1.3.2 2.5.6 3.6.1.3 0 .7-.2 1z"/></svg>
        <span>123 456 789</span>
      </li>
      <li>
        <svg viewBox="0 0 24 24" aria-hidden="true"><path fill="currentColor" d="M3 5h18a1 1 0 0 1 1 1v12a1 1 0 0 1-1 1H3a1 1 0 0 1-1-1V6a1 1 0 0 1 1-1zm1 2.2V17h16V7.2l-8 5.3z M5 7l7 4.6L19 7z"/></svg>
        <span>info@yourmail.com</span>
      </li>
      <li>
        <svg viewBox="0 0 24 24" aria-hidden="true"><circle cx="12" cy="12" r="9" fill="none" stroke="currentColor" stroke-width="2"/><path d="M3 12h18M12 3c3 3 3 15 0 18M12 3c-3 3-3 15 0 18" fill="none" stroke="currentColor" stroke-width="1.6"/></svg>
        <span>www.yourwebsite.com</span>
      </li>
    </ul>

    <div class="brand">
      <span class="brand-square" aria-hidden="true"></span>
      <p class="brand-name">Cedar Ridge<br>Mechanical</p>
    </div>
  </section>
</body>
</html>
```